Card Design for my dog training business Brightpaw Obedience

Need a business card design for my dog training business with my new logo. Want the card to come off professional yet fun. Want it to be very eye catchy as well. I normally have these at vet clinics, pet stores, and groomers. so need it to look better than my competitors.
Target Market(s)
dog owners
Industry/Entity Type
Dog Training
Contact Information for Business Card
needs logo, my name and info
Font styles to use
Serif
Colors
0255a3
ffffff
ec1f27
000000
333333
fbfbfb
Requirements
Must have
- Brightpaw Obedience
- Felix Orland
- 415 903 2276
- info@brightpawobedience.example
- www.brightpawobedience.example

```html
<!DOCTYPE html>
<html lang="en">
<head>
<meta charset="utf-8">
<title>Brightpaw Obedience – Business Card</title>
<link rel="stylesheet" href="https://fonts.googleapis.com/css2?family=Libre+Baskerville:ital,wght@0,400;0,700;1,400;1,700&family=Crimson+Text:ital@1&display=swap">
<style>
  :root {
    --backdrop: #161618;
    --card: #1f2023;
    --card-edge: #2a2b2f;
    --ink: #ffffff;
    --ink-soft: #d9d9d9;
    --accent: #e0262b;
    --gloss: #55575c;
  }
  * { box-sizing: border-box; margin: 0; padding: 0; }
  html, body {
    width: 1200px; height: 800px; overflow: hidden;
    background: var(--backdrop);
    font-family: "Libre Baskerville", Georgia, serif;
  }
  .stage {
    width: 1200px; height: 800px;
    display: flex; align-items: center; justify-content: center; gap: 40px;
  }
  .card {
    position: relative;
    width: 540px; height: 309px;
    border-radius: 18px;
    background: var(--card);
    box-shadow: 0 18px 40px rgba(0,0,0,.55), inset 0 0 0 1px var(--card-edge);
    overflow: hidden;
  }

  /* back side */
  .card--back { display: flex; align-items: center; justify-content: center; }
  .brand-mark--gloss {
    color: var(--gloss);
    font-size: 30px; font-weight: 700;
    text-align: center; line-height: 1.25;
  }

  /* front side */
  .identity { position: absolute; left: 40px; top: 42px; }
  .identity__name {
    color: var(--ink); font-weight: 700;
    font-size: 22px; letter-spacing: 1px; text-transform: uppercase;
  }
  .identity__role { color: var(--accent); font-size: 15px; margin-top: 2px; }

  .hours { position: absolute; left: 40px; top: 128px; font-style: italic; }
  .hours__label { color: var(--accent); font-size: 14px; font-weight: 700; }
  .hours__days { color: var(--ink); font-size: 14px; font-weight: 700; margin-top: 3px; }
  .hours__time { color: var(--ink-soft); font-size: 13px; font-style: normal; margin-top: 3px; }

  .contacts { position: absolute; left: 40px; bottom: 34px; list-style: none; }
  .contacts li {
    display: flex; align-items: center; gap: 10px;
    color: var(--ink); font-size: 12px; line-height: 22px;
  }
  .contacts svg { width: 14px; height: 14px; flex: none; }

  .brand { position: absolute; right: 34px; top: 52px; width: 210px; text-align: center; }
  .brand-mark--white {
    color: var(--ink); font-size: 24px; font-weight: 700; line-height: 1.25;
  }
  .brand__tagline {
    margin-top: 18px;
    font-family: "Crimson Text", Georgia, serif; font-style: italic;
    color: var(--ink-soft); font-size: 12px;
  }
</style>
</head>
<body>
<main class="stage">

  <section class="card card--back" aria-label="Card back">
    <div class="brand-mark brand-mark--gloss">Brightpaw<br>Obedience</div>
  </section>

  <section class="card card--front" aria-label="Card front">
    <div class="identity">
      <h1 class="identity__name">Felix Orland</h1>
      <p class="identity__role">Trainer</p>
    </div>

    <div class="hours">
      <p class="hours__label">Open:</p>
      <p class="hours__days">Tuesday to Sunday</p>
      <p class="hours__time">8.30AM to 6.30PM</p>
    </div>

    <ul class="contacts">
      <li>
        <svg viewBox="0 0 16 16" aria-hidden="true"><path fill="var(--accent)" d="M3.5 1.5l2.5 0 1 3.2-1.6 1.1c.8 1.9 2.4 3.5 4.3 4.3l1.1-1.6 3.2 1v2.5c0 .8-.7 1.5-1.5 1.5C6.7 13.5 2 8.8 2 3c0-.8.7-1.5 1.5-1.5z"/></svg>
        415 903 2276
      </li>
      <li>
        <svg viewBox="0 0 16 16" aria-hidden="true"><rect x="1" y="3" width="14" height="10" rx="1" fill="var(--accent)"/><polyline points="1.5,3.8 8,9 14.5,3.8" fill="none" stroke="var(--card)" stroke-width="1.3"/></svg>
        info@brightpawobedience.example
      </li>
      <li>
        <svg viewBox="0 0 16 16" aria-hidden="true"><circle cx="8" cy="8" r="7" fill="var(--accent)"/><g fill="none" stroke="var(--card)" stroke-width="1"><ellipse cx="8" cy="8" rx="3" ry="7"/><line x1="1" y1="8" x2="15" y2="8"/><line x1="2" y1="4.5" x2="14" y2="4.5"/><line x1="2" y1="11.5" x2="14" y2="11.5"/></g></svg>
        www.brightpawobedience.example
      </li>
    </ul>

    <div class="brand">
      <div class="brand-mark brand-mark--white">Brightpaw<br>Obedience</div>
      <p class="brand__tagline">“Good manners taught with patience and play.”</p>
    </div>
  </section>

</main>
</body>
</html>
```